Bramwell IT Services Business Card

Bramwell IT Services are a Perth based IT Services company. We would like to incorporate our company logo (attached) and stick with the blue that is in that design. I would like a clean look design that isn't too busy, yet creates a lasting image that is instantly recognisable in the recipients mind.

Target Market(s)

The target audience is small/medium business owners.

Industry/Entity Type

Business

Font styles to use
Serif
Sans Serif

Colors

Designer to choose colors to be used in the design.

Requirements
Must have
• The design should include:
Business name: Bramwell IT Services
Directors Name: Marcus Tenley
Phone Number: 0483 562 904
Email: support@bramwellit.com.au
Website: www.bramwellit.com.au

```html
<!DOCTYPE html>
<html lang="en">
<head>
<meta charset="utf-8">
<title>Bramwell IT Services – Business Card</title>
<link href="https://fonts.googleapis.com/css2?family=Questrial&display=swap" rel="stylesheet">
<style>
  :root {
    --page-bg: #e9eaec;
    --card-white: #f7f8fa;
    --card-black: #07090c;
    --card-black-edge: #151a20;
    --brand-blue: #1a73d9;
    --band-blue: #0a9be6;
    --text-light: #e6e9ee;
    --text-white: #ffffff;
  }
  * { margin: 0; padding: 0; box-sizing: border-box; }
  html, body {
    width: 1200px; height: 900px; overflow: hidden;
    background: var(--page-bg);
    font-family: "Questrial", sans-serif;
  }
  .sheet {
    width: 1200px; height: 900px;
    display: flex; flex-direction: column;
    align-items: center; justify-content: center; gap: 40px;
  }
  .card {
    width: 640px; height: 366px; position: relative; overflow: hidden;
    box-shadow: 0 6px 18px rgba(0,0,0,.18);
  }
  /* Front */
  .card--front {
    background: var(--card-white);
    display: flex; align-items: center; justify-content: center; gap: 14px;
  }
  .brand-mark {
    width: 26px; height: 26px; background: var(--brand-blue);
  }
  .brand-name {
    color: var(--brand-blue);
    font-size: 34px; letter-spacing: 1px; text-transform: uppercase;
  }
  /* Back */
  .card--back {
    background: linear-gradient(135deg, var(--card-black-edge) 0%, var(--card-black) 55%);
  }
  .back-brand {
    position: absolute; top: 62px; right: 40px;
    color: var(--brand-blue);
    font-size: 22px; letter-spacing: 1px; text-transform: uppercase;
  }
  .name-band {
    position: absolute; top: 130px; left: 300px; right: 0; height: 56px;
    background: var(--band-blue);
    border-radius: 6px 0 0 6px;
    display: flex; align-items: center; padding-left: 26px;
  }
  .director-name {
    color: var(--text-white); font-size: 28px; font-weight: 400;
  }
  .contact-list {
    position: absolute; left: 60px; top: 216px;
    list-style: none; display: flex; flex-direction: column; gap: 14px;
  }
  .contact-item {
    display: flex; align-items: baseline; gap: 22px;
    color: var(--text-light); font-size: 19px; letter-spacing: .5px;
  }
  .contact-label {
    color: var(--band-blue); font-size: 14px; width: 12px;
  }
</style>
</head>
<body>
  <main class="sheet">
    <section class="card card--front" aria-label="Card front">
      <span class="brand-mark" aria-hidden="true"></span>
      <span class="brand-name">Bramwell IT Services</span>
    </section>

    <section class="card card--back" aria-label="Card back">
      <p class="back-brand">Bramwell IT Services</p>
      <div class="name-band">
        <h1 class="director-name">Marcus Tenley</h1>
      </div>
      <ul class="contact-list">
        <li class="contact-item"><span class="contact-label">P</span>0483 562 904</li>
        <li class="contact-item"><span class="contact-label">E</span>support@bramwellit.com.au</li>
        <li class="contact-item"><span class="contact-label">W</span>www.bramwellit.com.au</li>
      </ul>
    </section>
  </main>
</body>
</html>
```